The Plate Compass

Cutting Through the Noise to What Actually Works.

Nutrition book

Target Market(s)

People looking to be or get healthy and eat right.

```html
<!DOCTYPE html>
<html lang="en">
<head>
<meta charset="utf-8">
<title>The Plate Compass — Book Cover</title>
<link rel="stylesheet" href="https://fonts.googleapis.com/css2?family=Bebas+Neue&family=Roboto+Condensed:wght@500;700&display=swap">
<style>
  :root {
    --backdrop: #bdbebf;
    --paper: #ffffff;
    --ink: #1a1414;
    --accent-red: #c32129;
    --fine-print: #8a8a8a;
    --tri-blue: #2e8fd1;
    --tri-green: #a9c98a;
    --tri-red: #d9333c;
    --tri-orange: #ee8a2c;
  }
  * { margin: 0; padding: 0; box-sizing: border-box; }
  html, body { width: 1200px; height: 1200px; overflow: hidden; }
  body { background: var(--backdrop); position: relative; }

  .book-cover {
    position: absolute;
    left: 360px; top: 240px;
    width: 480px; height: 719px;
    background: var(--paper);
    overflow: hidden;
  }

  .cover-title {
    position: absolute;
    left: 0; right: 0; top: 28px;
    text-align: center;
    font-family: "Bebas Neue", "Oswald", sans-serif;
    font-weight: 400;
    line-height: 0.82;
    color: var(--ink);
  }
  .cover-title span { display: block; }
  .title-lead { font-size: 92px; }
  .title-key { font-size: 146px; color: var(--accent-red); margin-top: 6px; }
  .title-tail { font-size: 110px; margin-top: 4px; letter-spacing: 3px; }

  .food-spread { position: absolute; left: 0; top: 0; width: 480px; height: 719px; }

  .food-label {
    position: absolute;
    font-family: "Roboto Condensed", "Arial Narrow", sans-serif;
    font-weight: 700;
    font-size: 12px;
    line-height: 1.1;
    color: var(--ink);
  }
  .food-label small {
    display: block;
    width: 64px;
    margin-top: 3px;
    font-size: 4.5px;
    line-height: 1.35;
    font-weight: 500;
    color: var(--fine-print);
  }
  .food-label.upper { text-transform: uppercase; }

  .author-name {
    position: absolute;
    left: 232px; top: 636px;
    font-family: "Bebas Neue", "Oswald", sans-serif;
    font-size: 52px;
    line-height: 1;
    color: var(--ink);
    letter-spacing: 0.5px;
  }
</style>
</head>
<body>
  <main class="book-cover">
    <svg class="food-spread" viewBox="0 0 480 719" role="img" aria-label="Overhead photograph of fresh whole foods — fruits, vegetables, nuts, grains and leafy greens — arranged in a diagonal band rising to the right">
      <defs>
        <linearGradient id="produceTones" x1="0" y1="1" x2="1" y2="0">
          <stop offset="0" stop-color="#c7d56a"/>
          <stop offset="0.25" stop-color="#e9b23a"/>
          <stop offset="0.45" stop-color="#c9714a"/>
          <stop offset="0.6" stop-color="#6d9c42"/>
          <stop offset="0.8" stop-color="#d2a24a"/>
          <stop offset="1" stop-color="#c8413d"/>
        </linearGradient>
      </defs>
      <polygon fill="url(#produceTones)" opacity="0.85"
        points="0,560 120,500 210,430 300,350 380,300 440,270 480,250 480,420 430,470 360,520 290,560 210,610 140,650 80,690 40,719 0,719"/>
      <polygon class="shape-tri" fill="var(--tri-blue)" points="108,463 114,451 120,463"/>
      <polygon class="shape-tri" fill="var(--tri-green)" points="133,437 143,437 138,445"/>
      <polygon class="shape-tri" fill="var(--tri-red)" points="414,496 426,501 415,508"/>
      <polygon class="shape-tri" fill="var(--tri-green)" points="420,508 428,512 421,516"/>
      <polygon class="shape-tri" fill="var(--tri-orange)" points="90,693 104,693 97,704"/>
    </svg>

    <h1 class="cover-title">
      <span class="title-lead">The</span>
      <span class="title-key">Plate</span>
      <span class="title-tail">Compass</span>
    </h1>

    <div class="food-label" style="left:318px; top:328px;">Quinoa<small>Complete plant protein for steady energy</small></div>
    <div class="food-label" style="left:238px; top:360px;">Quinoa<br>Oats<small>Soluble fiber that keeps you full</small></div>
    <div class="food-label" style="left:153px; top:398px;">Berries<small>Bright antioxidants in every small handful</small></div>
    <div class="food-label" style="left:24px; top:484px;">Berries<small>Low sugar fruit for daily snacks</small></div>
    <div class="food-label upper" style="left:431px; top:456px;">Whole<br>Grains</div>
    <div class="food-label" style="left:343px; top:518px;">Brown Rice<small>Slow carbs that fuel long days</small></div>
    <div class="food-label" style="left:277px; top:557px;">Wild Rice<small>Nutty grain rich in key minerals</small></div>
    <div class="food-label" style="left:112px; top:649px;">Vegetables<small>Fill half your plate with color</small></div>

    <p class="author-name">Author Name</p>
  </main>
</body>
</html>
```